Falkrin homes and renovations business card design.

Would like some new card designs utilizing my new logo that look professional. I am open to different colors on the logo or utilize the same ones we have. I like the original concept but would like to see some fresh ideas and build on what we have already done.

Target Market(s)

Custom home building industry, Real estate sales, Renovation projects.

Industry/Entity Type

Home Builder

Contact Information for Business Card

Falkrin Homes and Renovations
2871 96th Avenue
Halden Ridge, Northvale
T2R3W8
Home : 403- 718-4063 Cell: 403- 294-5170

My info is : Dax Falkrin, President and CEO
email: falkrinhomes@maildrop-example.net
Website: falkrinhomes-example.com
websit

Requirements
Must have
• Must Use my new logo design. I am open to different colors on the logo or utilize the same ones in the existing design. I can upload the original logo design if needed.

```html
<!DOCTYPE html>
<html lang="en">
<head>
<meta charset="utf-8">
<title>Falkrin Homes and Renovations – Business Card</title>
<link rel="stylesheet" href="https://fonts.googleapis.com/css2?family=Raleway:wght@400;500;600;700&display=swap">
<style>
  :root {
    --stage: #e2e2e4;
    --charcoal: #414042;
    --paper: #ffffff;
    --gold: #b5892f;
    --yellow: #f7b718;
    --muted: #7a7a7a;
    --light: #ffffff;
  }
  * { margin: 0; padding: 0; box-sizing: border-box; }
  html, body { width: 1200px; height: 800px; overflow: hidden; }
  body {
    background: var(--stage);
    font-family: "Raleway", sans-serif;
    position: relative;
  }
  .card {
    position: absolute;
    left: 281px;
    width: 638px;
    height: 354px;
    overflow: hidden;
  }
  .card--front { top: 20px; background: var(--paper); }
  .card--back { top: 414px; background: var(--charcoal); }

  .card__wave { position: absolute; inset: 0; width: 100%; height: 100%; }

  .brand {
    position: absolute;
    color: var(--gold);
    font-weight: 700;
    text-align: center;
    line-height: 1;
  }
  .brand__name { display: block; letter-spacing: 0.5px; }
  .brand__tagline { display: block; letter-spacing: 0.6px; }
  .card--front .brand { left: 48px; top: 118px; width: 206px; }
  .card--front .brand__name { font-size: 38px; }
  .card--front .brand__tagline { font-size: 13px; margin-top: 4px; }
  .card--back .brand { left: 0; width: 100%; top: 194px; }
  .card--back .brand__name { font-size: 52px; }
  .card--back .brand__tagline { font-size: 18px; margin-top: 4px; }

  .person {
    position: absolute;
    right: 32px;
    top: 56px;
    width: 210px;
    text-align: center;
  }
  .person__name { color: var(--yellow); font-size: 31px; font-weight: 500; line-height: 1; }
  .person__title { color: var(--muted); font-size: 16px; font-weight: 400; margin-top: 2px; }

  .contact {
    position: absolute;
    display: flex;
    align-items: center;
    color: var(--light);
    font-size: 19px;
    line-height: 24px;
  }
  .contact__icon {
    flex: none;
    width: 34px;
    height: 34px;
    border-radius: 50%;
    background: var(--yellow);
    display: flex;
    align-items: center;
    justify-content: center;
    margin-right: 18px;
  }
  .contact__icon svg { width: 20px; height: 20px; }
  .contact--email { left: 25px; top: 260px; }
  .contact--web { left: 25px; top: 301px; }
  .contact--web .contact__text, .contact--email .contact__text { font-size: 18px; }
  .contact--phone { left: 415px; top: 216px; }
  .contact--address { left: 415px; top: 271px; }
  .contact--address .contact__text { font-size: 18px; }
</style>
</head>
<body>

<section class="card card--front" aria-label="Business card front">
  <svg class="card__wave" viewBox="0 0 638 354" aria-hidden="true">
    <path fill="#414042" d="M0 226 C90 208 200 212 300 226 C400 236 460 145 638 145 L638 354 L0 354 Z"/>
    <path fill="#ffffff" d="M0 240 C100 230 220 246 310 216 C250 256 120 246 0 252 Z"/>
  </svg>

  <div class="brand">
    <span class="brand__name">FALKRIN</span>
    <span class="brand__tagline">HOMES AND RENOVATIONS</span>
  </div>

  <div class="person">
    <div class="person__name">Dax Falkrin</div>
    <div class="person__title">President and CEO</div>
  </div>

  <div class="contact contact--email">
    <span class="contact__icon">
      <svg viewBox="0 0 20 20" fill="none" stroke="#414042" stroke-width="1.5"><rect x="2" y="5" width="16" height="11"/><path d="M2 5 L10 12 L18 5 M2 16 L8 10 M18 16 L12 10"/></svg>
    </span>
    <span class="contact__text">falkrinhomes@maildrop-example.net</span>
  </div>
  <div class="contact contact--web">
    <span class="contact__icon">
      <svg viewBox="0 0 20 20" fill="none" stroke="#414042" stroke-width="1.4"><circle cx="10" cy="10" r="7.5"/><ellipse cx="10" cy="10" rx="3.5" ry="7.5"/><path d="M2.5 10 H17.5 M4 6 H16 M4 14 H16"/></svg>
    </span>
    <span class="contact__text">www.falkrinhomes-example.com</span>
  </div>
  <div class="contact contact--phone">
    <span class="contact__icon">
      <svg viewBox="0 0 20 20" fill="none" stroke="#414042" stroke-width="1.6"><rect x="6" y="2.5" width="8" height="15" rx="1.5"/><path d="M9 15 H11"/></svg>
    </span>
    <span class="contact__text">403- 718-4063<br>403- 294-5170</span>
  </div>
  <div class="contact contact--address">
    <span class="contact__icon">
      <svg viewBox="0 0 20 20"><path fill="#414042" d="M10 1.5 C6.4 1.5 4 4.2 4 7.4 C4 11.6 10 18.5 10 18.5 C10 18.5 16 11.6 16 7.4 C16 4.2 13.6 1.5 10 1.5 Z"/><circle cx="10" cy="7.4" r="2.2" fill="#f7b718"/></svg>
    </span>
    <span class="contact__text">2871 96th Avenue<br>Halden Ridge, Northvale</span>
  </div>
</section>

<section class="card card--back" aria-label="Business card back">
  <div class="brand">
    <span class="brand__name">FALKRIN</span>
    <span class="brand__tagline">HOMES AND RENOVATIONS</span>
  </div>
</section>

</body>
</html>
```